Workshop PPT Update for AI Transformation Sessions

Our strategic consulting firm runs strategy workshops using slides as workshop exercises. These slides are used to communicate to the participants in advance, run the workshops and produce the final deliverable.

It is time for a design "upgrade". We'd like them to be more engaging, hipper and more interesting. These slides are utilitarian, so clean and usable is good. I have attached the example of what we have today. I have also attached an example of another company's slides that I like.

We can't rip off their design nor can we go away 100% from what we have. But I think it is possible to "update" our look to something closer to their look. Grey colors are fine with some color pop.

Slide styles needed are - 1) Cover Page, 2) Instructions Page, 3) Bullet list 4) Worksheet (place for participants to add content 5) Table, 6) Two column.

```html
<!DOCTYPE html>
<html lang="en">
<head>
<meta charset="utf-8">
<title>NorthPath – AI Transformation Workshop Slides</title>
<link href="https://fonts.googleapis.com/css2?family=Lato:wght@400;700&display=swap" rel="stylesheet">
<style>
:root{
  --red:#b84a40;
  --slate:#454a57;
  --ink:#3c3f47;
  --muted:#5a5e66;
  --light:#eceef2;
  --white:#ffffff;
  --canvas:#f6f6f7;
  --cell:#ffffff;
}
*{box-sizing:border-box;margin:0;padding:0}
html,body{width:1200px;height:4147px;overflow:hidden}
body{background:var(--canvas);font-family:'Lato',sans-serif;color:var(--ink);position:relative}
.slide{position:absolute;left:43px;width:1104px;height:621px;background:var(--white);box-shadow:0 4px 14px rgba(0,0,0,.22);overflow:hidden}
.slide.grey{background:var(--light)}
.slide.dark{background:var(--slate);color:var(--white)}
.t{position:absolute;line-height:30px;white-space:nowrap}
.accent{position:absolute;left:30px;top:29px;width:38px;height:4px;background:var(--red)}
.title{position:absolute;left:30px;top:37px;line-height:50px;font-size:41px;font-weight:400;color:var(--ink)}
.brand{position:absolute;right:28px;top:41px;font-size:20px;line-height:28px;color:var(--ink)}
.foot{position:absolute;bottom:13px;font-size:13px;line-height:18px;color:var(--muted)}
.foot.left{left:30px}.foot.right{right:37px}
.dark .foot{color:var(--white)}
.dot{position:absolute;width:10px;height:10px;background:var(--red);border-radius:50%}
.check{display:inline-block;width:16px;height:16px;margin-right:14px;vertical-align:-2px}
.card{position:absolute;left:29px;top:138px;width:363px;height:410px;border-radius:8px;color:var(--white);box-shadow:0 3px 8px rgba(0,0,0,.2)}
.card.red{background:var(--red)}
.card.slate{background:var(--slate)}
.card .t{left:38px;font-size:19px}
.b{font-weight:700}
.item{font-size:19px;font-weight:700;color:var(--ink)}
.desc{font-size:16px;color:var(--ink)}
.photo{position:absolute;left:565px;top:80px;width:506px;height:506px;border-radius:50%;background:radial-gradient(circle at 50% 40%,#e9e6e2,#c9c3bc 55%,#8e8880);border:6px solid var(--slate);border-top-color:#e4e4e6;border-left-color:#d0d0d4}
.band{position:absolute;left:0;top:544px;width:1104px;height:14px;background:linear-gradient(90deg,var(--red) 0%,var(--red) 30%,#5a4e55 48%,#9a9ca4 62%,#ffffff 78%,#ffffff 100%)}
.cover-brand{position:absolute;left:0;width:100%;top:176px;text-align:center;font-size:34px;line-height:44px}
.cover-accent{position:absolute;left:533px;top:265px;width:38px;height:4px;background:var(--red)}
.cover-title{position:absolute;left:0;width:100%;top:284px;text-align:center;font-size:54px;font-weight:700;line-height:62px}
.cover-sub{position:absolute;left:0;width:100%;top:362px;text-align:center;font-size:22px;line-height:32px}
.plan{position:absolute;left:29px;top:138px}
.hcell{position:absolute;top:0;height:42px;border-radius:6px;color:var(--white);font-size:16px;font-weight:700;line-height:42px;padding-left:20px}
.hcell.red{background:var(--red)}.hcell.slate{background:var(--slate)}
.cell{position:absolute;background:var(--cell);border-radius:6px;font-size:16px;color:var(--muted);display:flex;align-items:center;padding-left:18px;line-height:22px}
.cell small{font-size:13px;display:block}
.cell.top{align-items:flex-start;padding-top:12px}
.cell.num{padding-left:8px}
.para{position:absolute;width:460px;font-size:16px;line-height:29px;color:var(--ink)}
</style>
</head>
<body>
<svg width="0" height="0" style="position:absolute">
  <symbol id="tick" viewBox="0 0 16 16"><circle cx="8" cy="8" r="6.8" fill="none" stroke="currentColor" stroke-width="2"/><path d="M4.8 8.2l2.2 2.2 4.2-4.4" fill="none" stroke="currentColor" stroke-width="2" stroke-linecap="round" stroke-linejoin="round"/></symbol>
</svg>

<!-- Slide 1: Getting Started -->
<section class="slide" style="top:54px">
  <div class="accent"></div>
  <h1 class="title">Getting Started</h1>
  <div class="brand">NorthPath</div>
  <span class="dot" style="left:33px;top:209px"></span><div class="t" style="left:69px;top:199px;font-size:22px">Complete the Engagement Sizing Survey.</div>
  <span class="dot" style="left:33px;top:270px"></span><div class="t" style="left:69px;top:260px;font-size:22px">Collect relevant inputs.</div>
  <span class="dot" style="left:33px;top:331px"></span><div class="t" style="left:69px;top:321px;font-size:22px">Determine workshop participants &amp; date.</div>
  <span class="dot" style="left:33px;top:392px"></span><div class="t" style="left:69px;top:382px;font-size:22px">Send invites, to include pre-work.</div>
  <div class="photo" role="img" aria-label="Photo of a smiling team lead presenting a report to colleagues at a meeting table"></div>
  <div class="foot left">2024 NorthPath</div><div class="foot right">01</div>
</section>

<!-- Slide 2: Cover -->
<section class="slide dark" style="top:730px">
  <div class="cover-brand">NorthPath</div>
  <div class="cover-accent"></div>
  <h1 class="cover-title">Kickoff &amp; Discovery</h1>
  <div class="cover-sub">Sizing &amp; Scoping AI Transformation</div>
  <div class="band"></div>
  <div class="foot left">2024 NorthPath</div><div class="foot right">02</div>
</section>

<!-- Slide 3: Workshop Overview -->
<section class="slide grey" style="top:1403px">
  <div class="accent"></div>
  <h1 class="title">Workshop Overview</h1>
  <div class="brand">NorthPath</div>
  <div class="card red">
    <div class="t" style="top:33px"><span class="b">Participants:</span> Execs</div>
    <div class="t" style="top:61px"><span class="b">Duration:</span>&nbsp; 2 hrs.</div>
    <div class="t b" style="top:113px">Prep Work:</div>
    <div class="t" style="top:145px"><svg class="check"><use href="#tick"/></svg>Org Strategy</div>
    <div class="t" style="top:177px"><svg class="check"><use href="#tick"/></svg>2023 Goal Performance</div>
    <div class="t" style="top:207px"><svg class="check"><use href="#tick"/></svg>Existing policies</div>
    <div class="t" style="top:237px"><svg class="check"><use href="#tick"/></svg>Pre-thinking questions</div>
    <div class="t" style="top:327px;font-size:14px">Deliverables</div>
    <div class="t" style="top:353px;font-size:14px">Your Company's AI Playbook</div>
  </div>
  <span class="dot" style="left:507px;top:131px"></span>
  <div class="t item" style="left:531px;top:121px">Confirm Company Direction</div>
  <div class="t desc" style="left:531px;top:151px">Recap organizational purpose, values, vision &amp; winning strategy.</div>
  <span class="dot" style="left:507px;top:211px"></span>
  <div class="t item" style="left:531px;top:201px">Develop AI Vision</div>
  <span class="dot" style="left:507px;top:262px"></span>
  <div class="t item" style="left:531px;top:252px">Develop AI Guiding Principles</div>
  <div class="t desc" style="left:531px;top:283px">Developed AI Guiding Principles, supporting policies to include</div>
  <div class="t desc" style="left:531px;top:310px">approved tools.</div>
  <span class="dot" style="left:507px;top:366px"></span>
  <div class="t item" style="left:531px;top:356px">Agree on a Governance Approach</div>
  <div class="t desc" style="left:531px;top:387px">Agreed upon governance approach, structure, &amp; executive champion.</div>
  <span class="dot" style="left:507px;top:441px"></span>
  <div class="t item" style="left:531px;top:431px">Agree on a Training &amp; Learning Approach</div>
  <div class="t desc" style="left:531px;top:462px">Set approach to training &amp; continuous learning.</div>
  <span class="dot" style="left:507px;top:517px"></span>
  <div class="t item" style="left:531px;top:507px">Determine Rollout &amp; Communication</div>
  <div class="t desc" style="left:531px;top:535px">Organizational rollout &amp; continuous communication.</div>
  <div class="foot left">2024 NorthPath</div><div class="foot right">03</div>
</section>

<!-- Slide 4: Instructions -->
<section class="slide grey" style="top:2077px">
  <div class="accent"></div>
  <h1 class="title">Creating your AI Guiding Principles</h1>
  <div class="brand">NorthPath</div>
  <div class="card slate">
    <div class="t b" style="top:34px">Your Existing Material</div>
    <div class="t" style="top:65px"><svg class="check"><use href="#tick"/></svg>Company Values</div>
    <div class="t" style="top:97px"><svg class="check"><use href="#tick"/></svg>Current Policies</div>
    <div class="t" style="top:127px;left:75px">(GDPR, CCPA, etc.)</div>
    <div class="t" style="top:157px"><svg class="check"><use href="#tick"/></svg>Legal Guidance</div>
    <div class="t" style="top:189px"><svg class="check"><use href="#tick"/></svg>OTHER</div>
    <div class="t b" style="top:258px">Examples for Inspiration</div>
    <div class="t" style="top:287px">See next slides</div>
    <div class="t b" style="top:327px">PromptMate Prompts</div>
    <div class="t" style="top:356px">HERE</div>
  </div>
  <div class="t desc b" style="left:501px;top:143px">Purpose:</div>
  <div class="t desc" style="left:501px;top:172px">To create behavioral statements that everyone is expected to adhere to.</div>
  <div class="t b" style="left:501px;top:211px;font-size:22px">Instructions:</div>
  <span class="dot" style="left:505px;top:264px"></span>
  <div class="t desc b" style="left:531px;top:254px;font-size:18px">Create the Outline.</div>
  <div class="t desc" style="left:531px;top:284px">Determine the topics that need a principle.</div>
  <span class="dot" style="left:505px;top:333px"></span>
  <div class="t desc b" style="left:531px;top:323px;font-size:18px">Audit the Outline.</div>
  <div class="t desc" style="left:531px;top:353px">Look at the current policies to determine if all topics are covered.</div>
  <span class="dot" style="left:505px;top:403px"></span>
  <div class="t desc b" style="left:531px;top:393px;font-size:18px">Draft the Guiding Principles.</div>
  <span class="dot" style="left:505px;top:441px"></span>
  <div class="t desc b" style="left:531px;top:431px;font-size:18px">Determine which GPs need detailed policies.</div>
  <span class="dot" style="left:505px;top:481px"></span>
  <div class="t desc b" style="left:531px;top:471px;font-size:18px">Determine which AI Tools support the GPs.</div>
  <span class="dot" style="left:505px;top:520px"></span>
  <div class="t desc b" style="left:531px;top:510px;font-size:18px">Finalize via a legal and executive review.</div>
  <div class="foot left">2024 NorthPath</div><div class="foot right">04</div>
</section>

<!-- Slide 5: Table -->
<section class="slide grey" style="top:2752px">
  <div class="accent"></div>
  <h1 class="title">Plan Structure</h1>
  <div class="brand">NorthPath</div>
  <div class="plan">
    <div class="hcell red" style="left:0;width:180px">Level</div>
    <div class="hcell slate" style="left:189px;width:270px">Planning Element &amp; Definition</div>
    <div class="hcell red" style="left:467px;width:270px">Accountability/Owner</div>
    <div class="hcell slate" style="left:745px;width:271px">Frequency of Modification</div>

    <div class="cell num" style="left:0;top:52px;width:48px;height:71px">1</div>
    <div class="cell" style="left:57px;top:52px;width:123px;height:71px">What<br>(overall)</div>
    <div class="cell" style="left:189px;top:52px;width:270px;height:71px">Strategic Priorities</div>
    <div class="cell" style="left:467px;top:52px;width:270px;height:71px">N/A</div>
    <div class="cell" style="left:745px;top:52px;width:271px;height:71px">3+ years</div>

    <div class="cell num" style="left:0;top:133px;width:48px;height:71px">1.1</div>
    <div class="cell" style="left:57px;top:133px;width:123px;height:71px">What<br>(this year)</div>
    <div class="cell" style="left:189px;top:133px;width:270px;height:71px"><span>Goals<small>Outcomes &amp; Strategies</small></span></div>
    <div class="cell" style="left:467px;top:133px;width:270px;height:71px">Executive Leadership</div>
    <div class="cell" style="left:745px;top:133px;width:271px;height:71px">1-3 years</div>

    <div class="cell num" style="left:0;top:213px;width:48px;height:71px">1.1.1</div>
    <div class="cell top" style="left:57px;top:213px;width:123px;height:151px">How</div>
    <div class="cell" style="left:189px;top:213px;width:270px;height:71px">Key Performance Indicators<br>and/or Initiatives</div>
    <div class="cell" style="left:467px;top:213px;width:270px;height:71px"></div>
    <div class="cell" style="left:745px;top:213px;width:271px;height:71px">1 year<br>(w/ qrtly targets)</div>

    <div class="cell num" style="left:0;top:293px;width:48px;height:71px">1.1.<br>1.1</div>
    <div class="cell" style="left:189px;top:293px;width:270px;height:71px">Action Items</div>
    <div class="cell" style="left:467px;top:293px;width:270px;height:71px"></div>
    <div class="cell" style="left:745px;top:293px;width:271px;height:71px">Quarterly/Monthly</div>
  </div>
  <div class="foot left">2024 NorthPath</div><div class="foot right">05</div>
</section>

<!-- Slide 6: Two column -->
<section class="slide" style="top:3427px">
  <div class="accent"></div>
  <h1 class="title">AI Guiding Principles</h1>
  <div class="brand">NorthPath</div>
  <div class="t desc" style="left:29px;top:91px">What guides our decision-making and approach?</div>

  <span class="dot" style="left:34px;top:166px"></span>
  <div class="t item" style="left:62px;top:156px;font-size:18px">Principle #1</div>
  <p class="para" style="left:62px;top:185px">Complete perspective from Executives, Directors, Managers<br>&amp; Staff. Conduct competitive analysis and customer research<br>(optional).</p>

  <span class="dot" style="left:34px;top:297px"></span>
  <div class="t item" style="left:62px;top:287px;font-size:18px">Principle #2</div>
  <p class="para" style="left:62px;top:316px">Complete perspective from Executives, Directors, Managers<br>&amp; Staff. Conduct competitive analysis and customer research<br>(optional).</p>

  <span class="dot" style="left:34px;top:429px"></span>
  <div class="t item" style="left:62px;top:419px;font-size:18px">Principle #3</div>
  <p class="para" style="left:62px;top:448px">Complete perspective from Executives, Directors, Managers<br>&amp; Staff. Conduct competitive analysis and customer research<br>(optional).</p>

  <span class="dot" style="left:569px;top:166px"></span>
  <div class="t item" style="left:597px;top:156px;font-size:18px">Principle #4</div>
  <p class="para" style="left:597px;top:185px">Complete perspective from Executives, Directors, Managers<br>&amp; Staff. Conduct competitive analysis and customer research<br>(optional).</p>

  <span class="dot" style="left:569px;top:297px"></span>
  <div class="t item" style="left:597px;top:287px;font-size:18px">Principle #5</div>
  <p class="para" style="left:597px;top:316px">Complete perspective from Executives, Directors, Managers<br>&amp; Staff. Conduct competitive analysis and customer research<br>(optional).</p>

  <div class="foot left">2024 NorthPath</div><div class="foot right">06</div>
</section>

</body>
</html>
```